business card deign

Logo needs the following on it.
1. attached logo
2. Tagline - "If it keeps a drink cold or the party going...we do it!"
3. Name- Dalton Pikes, Founder and CPO
4. Address - 412 E. Carver Avenue, Ste 2207, Tampa, FL. 33917
5. Phone - 555.318.4726

```html
<!DOCTYPE html>
<html lang="en">
<head>
<meta charset="utf-8">
<title>Kestra Business Card</title>
<link rel="stylesheet" href="https://fonts.googleapis.com/css2?family=Montserrat:wght@400;700&display=swap">
<style>
  :root {
    --backdrop: #8e8e8e;
    --card-dark: #1f1f1f;
    --card-light: #ffffff;
    --ink: #111111;
    --ink-soft: #333333;
    --paper-text: #f2f2f2;
  }
  * { box-sizing: border-box; margin: 0; padding: 0; }
  html, body { width: 1200px; height: 900px; overflow: hidden; }
  body {
    background: var(--backdrop);
    font-family: "Montserrat", sans-serif;
    display: flex;
    flex-direction: column;
    align-items: center;
    justify-content: center;
    gap: 40px;
  }
  .card {
    width: 640px;
    height: 366px;
    position: relative;
    box-shadow: 0 10px 24px rgba(0,0,0,0.3);
  }
  .card--front { background: var(--card-dark); color: var(--paper-text); }
  .card--back { background: var(--card-light); color: var(--ink); }

  .front-brand {
    position: absolute;
    top: 118px;
    left: 0; right: 0;
    display: flex;
    align-items: center;
    justify-content: center;
    gap: 18px;
  }
  .brand-dot {
    width: 28px; height: 28px;
    border-radius: 50%;
    background: var(--paper-text);
  }
  .wordmark {
    font-weight: 700;
    font-size: 40px;
    letter-spacing: 0.45em;
    margin-right: -0.45em;
  }
  .tagline {
    position: absolute;
    bottom: 52px;
    left: 0; right: 0;
    text-align: center;
    font-size: 13px;
    font-weight: 400;
  }

  .back-wordmark {
    position: absolute;
    top: 52px; left: 48px;
    font-size: 32px;
    color: var(--ink);
  }
  .contact {
    position: absolute;
    top: 136px; left: 48px;
  }
  .contact__name { font-size: 22px; font-weight: 700; }
  .contact__role { font-size: 13px; color: var(--ink-soft); margin-top: 2px; }
  .contact__address { font-size: 13px; color: var(--ink-soft); margin-top: 22px; line-height: 1.4; }
  .contact__list { list-style: none; margin-top: 20px; }
  .contact__list li {
    display: flex; align-items: center; gap: 10px;
    font-size: 13px; color: var(--ink-soft);
    margin-bottom: 8px;
  }
  .contact__list svg { width: 14px; height: 14px; fill: var(--ink); }
  .back-mark {
    position: absolute;
    right: 70px; top: 90px;
    width: 190px; height: 190px;
    border-radius: 50%;
    background: var(--ink);
  }
</style>
</head>
<body>
  <section class="card card--front">
    <div class="front-brand">
      <span class="brand-dot"></span>
      <span class="wordmark">KESTRA</span>
    </div>
    <p class="tagline">If it keeps a drink cold or the party going...we do it</p>
  </section>

  <section class="card card--back">
    <div class="wordmark back-wordmark">KESTRA</div>
    <div class="contact">
      <p class="contact__name">Dalton Pikes</p>
      <p class="contact__role">Founder and CPO</p>
      <p class="contact__address">412 E. Carver Avenue, Ste 2207,<br>Tampa, FL. 33917</p>
      <ul class="contact__list">
        <li>
          <svg viewBox="0 0 24 24" aria-hidden="true"><path d="M6.6 10.8a15.2 15.2 0 0 0 6.6 6.6l2.2-2.2a1 1 0 0 1 1-.25 11.4 11.4 0 0 0 3.6.57 1 1 0 0 1 1 1V20a1 1 0 0 1-1 1A17 17 0 0 1 3 4a1 1 0 0 1 1-1h3.5a1 1 0 0 1 1 1c0 1.25.2 2.45.57 3.57a1 1 0 0 1-.25 1z"/></svg>
          555.318.4726
        </li>
        <li>
          <svg viewBox="0 0 24 24" aria-hidden="true"><path d="M2 5h20v14H2z" fill="none"/><path d="M2 5h20v2l-10 6L2 7zm0 4.3l10 6 10-6V19H2z"/></svg>
          info@kestraco.com
        </li>
        <li>
          <svg viewBox="0 0 24 24" aria-hidden="true"><circle cx="12" cy="12" r="10"/></svg>
          www.kestraco.com
        </li>
      </ul>
    </div>
    <div class="back-mark" aria-hidden="true"></div>
  </section>
</body>
</html>
```